Flyer to advertise gutter cleaning throughout the Autumn and winter monthss

I need a new flyer to advertise gutter and driveway cleaning, roof and gutter repairs.

I am an experienced licensed Plumber and Gasfitter looking to broaden my scope of work to gutter cleaning. I am experienced in cleaning gutter and live in a area with large gum trees. I wont something that's clear, eye catching but not too busy.

Flyer requirements: Free roof inspection - no obligation. Gutter Cleaning from $199. Pictures of men using blower or hands to clean roof gutters (no obvious faces) to be included. Australian looking houses.

A mention that 'All general plumbing maintenance' is offered as other services but not too much wording about this as the target is for gutter cleaning.

Phone number: 0427 385 912 (in this format)
Business Name: Larkvale Plumbing & Gasfitting
License: 3175420
ABN: 71364058227
Web: http://larkvaleplumbing.example.site/

Target Market(s)

Elderly - busy working class

Industry/Entity Type

Plumber

Font styles to use
Sans Serif

Colors
0355a3
fbed22
ec1f27
f78f20

Requirements
Must have
• Roof Gutter Cleaning pictures
• Men in protective clothing if possible
Nice to have
• More information:
• Prevent against flooding, mold, rust, rotting and corrosion now!
• Gutter Cleaning Services
• • Remove leaves, sticks, and other debris
• • Clear away clogs
• • Test your downpipes
• • Pinpoint any gutter issues
• • Repair gutter
• With regular service, you can count on your property to be well-protected no matter what the forecast!
Should not have
• Houses that don't look Australian

```html
<!DOCTYPE html>
<html lang="en">
<head>
<meta charset="utf-8">
<title>Larkvale Plumbing &amp; Gasfitting – Gutter Cleaning Flyer</title>
<link rel="stylesheet" href="https://fonts.googleapis.com/css2?family=Open+Sans:wght@400;600;700;800&family=Oswald:wght@600;700&display=swap">
<style>
  :root {
    --blue-deep: #0a2a66;
    --blue: #0355a3;
    --blue-mid: #1a5fb0;
    --yellow: #f2cc16;
    --yellow-dark: #d9b20a;
    --white: #ffffff;
    --paper: #eef0f2;
    --paper-dark: #d9dde1;
    --ink-blue: #1f2f7a;
    --ring: #9aa1a8;
  }
  * { box-sizing: border-box; margin: 0; padding: 0; }
  html, body { width: 973px; height: 1200px; overflow: hidden; background: #ffffff; }
  .flyer {
    position: relative;
    width: 973px;
    height: 1200px;
    overflow: hidden;
    font-family: "Open Sans", Arial, sans-serif;
    background: var(--paper);
  }

  /* Hero photo area */
  .hero {
    position: absolute; left: 0; top: 0; width: 973px; height: 526px;
    background:
      linear-gradient(180deg, #4f86cf 0%, #a9c6ea 22%, #eef1f4 45%, #dde1e6 68%, #5f8c3a 82%, #3f7326 100%);
  }
  .brand {
    position: absolute; top: 42px; right: 38px;
    display: flex; align-items: center; gap: 14px;
  }
  .brand-dot {
    width: 58px; height: 58px; border-radius: 50%;
    background: var(--blue);
  }
  .brand-name {
    font-weight: 700; font-size: 21px; line-height: 1.15;
    color: var(--blue-deep); letter-spacing: -0.2px;
  }

  /* Headline band */
  .headline-band {
    position: absolute; left: 0; top: 526px; width: 973px; height: 127px;
    background: linear-gradient(90deg, var(--blue) 0%, var(--blue-mid) 45%, var(--blue-deep) 100%);
    display: flex; flex-direction: column; justify-content: center; align-items: center;
    color: var(--white); font-weight: 700; font-size: 35px; line-height: 1.35;
    text-align: center; letter-spacing: -0.3px;
  }

  /* Offers area */
  .offers {
    position: absolute; left: 0; top: 653px; width: 973px; height: 463px;
    background: radial-gradient(ellipse at 50% 40%, #fafbfc 0%, var(--paper) 55%, var(--paper-dark) 100%);
  }
  .offer {
    position: absolute; border-radius: 50%;
    display: flex; flex-direction: column; align-items: center; justify-content: center;
    text-align: center; color: var(--white);
  }
  .offer-ring {
    position: absolute; border-radius: 50%; border: 1.5px solid var(--ring);
  }
  .offer-ring.left { left: 47px; top: 38px; width: 290px; height: 290px; }
  .offer-ring.right { left: 617px; top: 38px; width: 290px; height: 290px; }
  .offer.photo { width: 262px; height: 262px; top: 52px; }
  .offer.gutter { left: 61px; background: radial-gradient(circle at 40% 35%, #7d8a72 0%, #4f5a4a 55%, #363f33 100%); }
  .offer.driveway { left: 631px; background: radial-gradient(circle at 55% 35%, #8a8d90 0%, #5c5f63 55%, #3b3d40 100%); }
  .offer-label {
    font-weight: 700; font-size: 25px; line-height: 1.3;
    text-shadow: 0 1px 3px rgba(0,0,0,0.45);
  }
  .offer-price {
    font-family: "Oswald", "Arial Narrow", sans-serif; font-weight: 700;
    font-size: 56px; line-height: 1.1; margin-top: 2px;
    text-shadow: 0 2px 4px rgba(0,0,0,0.5);
  }
  .offer.inspection {
    left: 330px; top: 30px; width: 308px; height: 308px;
    background: radial-gradient(circle at 50% 40%, #f7d82a 0%, var(--yellow) 60%, var(--yellow-dark) 100%);
    box-shadow: 0 26px 30px -18px rgba(0,0,0,0.35);
  }
  .offer.inspection::before {
    content: ""; position: absolute; inset: 10px; border-radius: 50%;
    border: 1.5px solid rgba(255,255,255,0.55);
  }
  .inspection-title {
    font-family: "Oswald", "Arial Narrow", sans-serif; font-weight: 700;
    font-size: 38px; line-height: 1.1; text-transform: uppercase;
  }
  .inspection-sub {
    font-weight: 700; font-size: 25px; margin-top: 4px;
  }
  .inspection-rule {
    width: 160px; height: 1.5px; background: rgba(255,255,255,0.85); margin: 14px 0 12px;
  }
  .inspection-meta { font-size: 16px; line-height: 1.5; }
  .website {
    position: absolute; left: 0; right: 0; top: 400px; text-align: center;
    font-weight: 700; font-size: 18px; color: var(--ink-blue);
  }

  /* Contact bar */
  .contact-bar { position: absolute; left: 0; top: 1116px; width: 973px; height: 84px; }
  .contact-bar-shape { position: absolute; left: 0; top: 0; }
  .contact-cta {
    position: absolute; left: 70px; top: 0; height: 84px;
    display: flex; align-items: center;
    color: var(--white); font-weight: 600; font-size: 32px; letter-spacing: -0.3px;
  }
  .contact-phone {
    position: absolute; left: 538px; top: 0; height: 84px;
    display: flex; align-items: center; gap: 18px;
    color: var(--white); font-weight: 700; font-size: 47px; letter-spacing: 1px;
    white-space: nowrap;
  }
  .phone-icon { flex: 0 0 44px; width: 44px; height: 44px; display: block; }
</style>
</head>
<body>
<main class="flyer">

  <section class="hero" role="img" aria-label="Photo of a two-storey weatherboard house with lawn and garden while a worker's arms hold a pressure washer wand"></section>

  <div class="brand">
    <span class="brand-dot"></span>
    <span class="brand-name">Larkvale Plumbing<br>&amp; Gasfitting</span>
  </div>

  <header class="headline-band">
    <span>GUTTER AND DRIVEWAY CLEANING</span>
    <span>ROOF AND GUTTER REPAIRS</span>
  </header>

  <section class="offers" role="group" aria-label="Offers">
    <div class="offer-ring left"></div>
    <div class="offer photo gutter" role="img" aria-label="Photo of a gutter being cleared of leaves with a spray nozzle">
      <span class="offer-label">GUTTER<br>CLEANING FROM</span>
      <span class="offer-price">$199</span>
    </div>

    <div class="offer-ring right"></div>
    <div class="offer photo driveway" role="img" aria-label="Photo of a driveway being pressure washed">
      <span class="offer-label">DRIVEWAY<br>CLEANING FROM</span>
      <span class="offer-price">$199</span>
    </div>

    <div class="offer inspection">
      <span class="inspection-title">Free Roof<br>Inspection</span>
      <span class="inspection-sub">NO OBLIGATION</span>
      <span class="inspection-rule"></span>
      <span class="inspection-meta">License: 3175420<br>ABN: 71364058227</span>
    </div>

    <p class="website">www.larkvaleplumbing.example.site</p>
  </section>

  <footer class="contact-bar">
    <svg class="contact-bar-shape" width="973" height="84" viewBox="0 0 973 84" aria-hidden="true">
      <defs>
        <linearGradient id="barBlue" x1="0" x2="1" y1="0" y2="0">
          <stop offset="0" stop-color="#0a2a66"/>
          <stop offset="1" stop-color="#0355a3"/>
        </linearGradient>
      </defs>
      <polygon points="0,0 488,0 460,84 0,84" fill="url(#barBlue)"/>
      <polygon points="488,0 496,0 468,84 460,84" fill="#ffffff"/>
      <polygon points="496,0 973,0 973,84 468,84" fill="#f2cc16"/>
    </svg>
    <span class="contact-cta">CONTACT US TODAY!!!</span>
    <span class="contact-phone">
      <svg class="phone-icon" width="44" height="44" viewBox="0 0 44 44" aria-hidden="true">
        <circle cx="22" cy="22" r="19.5" fill="none" stroke="#ffffff" stroke-width="3"/>
        <path d="M15.5 12.5c1-.8 2.2-.6 2.8.4l2 3.2c.5.9.3 2-.5 2.6l-1.3 1c.9 2 2.4 3.6 4.4 4.6l1-1.3c.6-.8 1.8-1 2.6-.5l3.2 2c1 .6 1.2 1.8.4 2.8l-1.4 1.6c-1 1.1-2.6 1.5-4 .9-5.3-2-9.3-6-11.3-11.3-.6-1.4-.2-3 .9-4z" fill="#ffffff"/>
      </svg>
      <span class="phone-number">0427 385 912</span>
    </span>
  </footer>

</main>
</body>
</html>
```